KORVAL:advise Business Cards

We need a business card design for KORVAL:advise (Logo Attached), a management consultancy specialized in brand & business building.

Design should be clean, smart and a touch of innnovation without being gimmicky.

The details on the card should be:
Name: Tomas Velduren
Title: Managing Director
Address: 42 Marlowe Pier, Tarn Vessel Tower, Singapore 073926
Tel: +6285927461082
email: tv@korvaladvise.example
website: korvaladvise.example

For further background on corporate identity, please check www.korvaladvise.example
Updates

Dear all,

Many thanks for the submissions so far! I gave feedback to those designs that I prefer at this stage.

Overall I see that my preference goes into the direction that 'less is more' and 'simple is beautiful'

Please create uniqueness and standout by the simplicity and attraction of the overall concept and design.

Many thanks and please shout incase of questions!

Tomas

Industry/Entity Type

Business

```html
<!DOCTYPE html>
<html lang="en">
<head>
<meta charset="utf-8">
<title>KORVAL:advise Business Cards</title>
<link rel="stylesheet" href="https://fonts.googleapis.com/css2?family=Open+Sans:wght@400;600;700&display=swap">
<style>
  :root {
    --canvas: #ecebe8;
    --paper: #ffffff;
    --brand-orange: #ff6600;
    --ink-dark: #4a4a4a;
    --ink-body: #3c3c3c;
    --card-edge: #2f2f2f;
  }
  * { margin: 0; padding: 0; box-sizing: border-box; }
  html, body {
    width: 1173px;
    height: 1200px;
    overflow: hidden;
    background: var(--canvas);
    font-family: "Open Sans", Arial, sans-serif;
  }
  .canvas { position: relative; width: 1173px; height: 1200px; }

  .card { position: absolute; }
  .card-front {
    left: 201px; top: 50px; width: 938px; height: 539px;
    background: var(--paper);
    border: 1.5px solid var(--card-edge);
  }
  .card-back {
    left: 40px; top: 623px; width: 942px; height: 538px;
    background: var(--brand-orange);
  }

  .wordmark {
    position: absolute;
    font-weight: 600;
    line-height: 1;
    white-space: nowrap;
    letter-spacing: -0.5px;
  }
  .card-front .wordmark {
    left: 30px; top: 46px;
    font-size: 80px;
    color: var(--ink-dark);
  }
  .card-back .wordmark {
    left: 0; right: 0; top: 180px;
    text-align: center;
    font-size: 100px;
    color: var(--paper);
  }

  .contact-list { position: absolute; left: 33px; top: 288px; list-style: none; }
  .contact-item {
    display: flex; align-items: center;
    height: 40px;
    font-size: 22px;
    color: var(--ink-body);
  }
  .contact-icon { width: 20px; height: 20px; margin-right: 7px; flex: none; }

  .address {
    position: absolute; left: 33px; top: 436px;
    font-size: 22px; line-height: 34px;
    color: var(--ink-body);
    font-style: normal;
  }

  .person { position: absolute; right: 26px; top: 328px; text-align: right; }
  .person-name { font-size: 27px; font-weight: 700; color: var(--ink-dark); line-height: 36px; }
  .person-title { font-size: 23px; color: var(--brand-orange); line-height: 34px; }

  .back-url {
    position: absolute; left: 0; right: 0; top: 377px;
    text-align: center;
    font-size: 24px;
    letter-spacing: 5px;
    color: var(--paper);
  }
</style>
</head>
<body>
<div class="canvas">

  <section class="card card-front" aria-label="Business card front">
    <div class="wordmark">KORVAL:advise</div>

    <ul class="contact-list">
      <li class="contact-item">
        <svg class="contact-icon" viewBox="0 0 20 20" aria-hidden="true">
          <circle cx="10" cy="10" r="9" fill="none" stroke="var(--brand-orange)" stroke-width="1.6"/>
          <path d="M7 5.5 L8.8 5.5 L9.4 8 L8.2 8.9 Q9.2 11.2 11.1 12 L12 10.8 L14.5 11.4 L14.5 13.2 Q10.5 14 8 11.5 Q5.8 9 7 5.5 Z" fill="var(--brand-orange)"/>
        </svg>
        +6285927461082
      </li>
      <li class="contact-item">
        <svg class="contact-icon" viewBox="0 0 20 20" aria-hidden="true">
          <rect x="2" y="5" width="16" height="11" rx="1.5" fill="var(--brand-orange)"/>
          <path d="M2.5 6 L10 11.5 L17.5 6" fill="none" stroke="#ffffff" stroke-width="1.6"/>
        </svg>
        tv@korvaladvise.example
      </li>
      <li class="contact-item">
        <svg class="contact-icon" viewBox="0 0 20 20" aria-hidden="true">
          <g fill="none" stroke="var(--brand-orange)" stroke-width="1.5">
            <circle cx="10" cy="10" r="8"/>
            <ellipse cx="10" cy="10" rx="3.5" ry="8"/>
            <line x1="2" y1="10" x2="18" y2="10"/>
            <path d="M3.5 6 H16.5 M3.5 14 H16.5"/>
          </g>
        </svg>
        www.korvaladvise.example
      </li>
    </ul>

    <address class="address">
      42 Marlowe Pier, Tarn<br>
      Vessel Tower, Singapore 073926
    </address>

    <div class="person">
      <div class="person-name">Tomas Velduren</div>
      <div class="person-title">Managing Director</div>
    </div>
  </section>

  <section class="card card-back" aria-label="Business card back">
    <div class="wordmark">KORVAL:advise</div>
    <div class="back-url">www.korvaladvise.example</div>
  </section>

</div>
</body>
</html>
```